Business Card for Multi-Brand Sportswear Company

We are looking for a business card which represents our company and the multiple brands within it.

The company: Fen Athletics (LTD)
The brands: Fen, TavaPuni, ElmStretch, Grit and Rain

Employees using these cards would be representing Fen Athletics, rather than any of the individual brands. You will see a current design within the uploaded files, to give some inspiration. The actual text of the brands is not necessary, but the logos should be on there is some format.

Our creative minds on this are stretched, so we are looking for someone to make this their own, and show us what a good business card should look like.

We may like to get these printed with spot gloss, so keep that in mind with your designs.

www.fenathletics.co.uk

Industry/Entity Type

Business

Contact Information for Business Card

Leo Pemberton-Hale
Operations Manager
(+44) 1632 960 418
Leo@fenathletics.co.uk
www.fenathletics.co.uk

Font styles to use
Sans Serif
Other font styles liked:
• Eurostile

Colors
ffffff

Requirements
Nice to have
• Dark (black) background

```html
<!DOCTYPE html>
<html lang="en">
<head>
<meta charset="utf-8">
<title>Fen Athletics – Business Card</title>
<link rel="stylesheet" href="https://fonts.googleapis.com/css2?family=Saira:ital,wght@0,400;0,600;1,400&display=swap">
<style>
  :root {
    --backdrop: #4a4a4a;
    --card-light: #ffffff;
    --card-dark: #000000;
    --accent-red: #e8202a;
    --ink: #1a1a1a;
    --ink-soft: #555555;
    --muted-grey: #8a8a8a;
    --muted-purple: #5c5260;
  }
  html, body {
    margin: 0;
    padding: 0;
    width: 1105px;
    height: 1200px;
    overflow: hidden;
    background: var(--backdrop);
    font-family: "Saira", sans-serif;
  }
  .card {
    position: absolute;
    left: 196px;
    width: 720px;
    height: 412px;
    box-sizing: border-box;
  }
  .card-front { top: 146px; background: var(--card-light); }
  .card-back  { top: 602px; background: var(--card-dark); }

  .company-name {
    position: absolute;
    left: 46px;
    top: 72px;
    margin: 0;
    font-size: 48px;
    font-weight: 600;
    color: var(--ink);
    letter-spacing: 1px;
    line-height: 1;
  }
  .person-name {
    position: absolute;
    left: 46px;
    top: 203px;
    margin: 0;
    font-size: 26px;
    font-weight: 600;
    color: var(--accent-red);
    line-height: 1;
    letter-spacing: 0.5px;
    white-space: nowrap;
  }
  .person-role {
    position: absolute;
    left: 46px;
    top: 234px;
    margin: 0;
    font-size: 20px;
    color: var(--ink);
    line-height: 1;
    white-space: nowrap;
  }
  .web-band {
    position: absolute;
    left: 0;
    top: 0;
  }
  .band-url {
    position: absolute;
    right: 18px;
    top: 229px;
    font-size: 18px;
    color: var(--card-light);
    letter-spacing: 2px;
    line-height: 34px;
    white-space: nowrap;
  }
  .contact-list {
    position: absolute;
    left: 46px;
    top: 284px;
    margin: 0;
    padding: 0;
    list-style: none;
  }
  .contact-item {
    display: flex;
    align-items: center;
    height: 29px;
    font-size: 19px;
    color: var(--ink-soft);
    white-space: nowrap;
  }
  .contact-item svg { width: 22px; height: 22px; margin-right: 8px; flex: none; }

  .brand-row {
    position: absolute;
    left: 0;
    right: 0;
    top: 188px;
    display: flex;
    justify-content: center;
    align-items: center;
    gap: 34px;
  }
  .brand {
    display: flex;
    align-items: center;
    gap: 8px;
    font-size: 24px;
    font-weight: 600;
    color: var(--card-light);
    line-height: 1;
    white-space: nowrap;
  }
  .brand-mark { width: 14px; height: 14px; flex: none; }
  .mark-circle { border-radius: 50%; background: var(--muted-grey); }
  .mark-square-purple { background: var(--muted-purple); }
  .mark-square-red { background: var(--accent-red); }
  .back-url {
    position: absolute;
    left: 0;
    right: 0;
    top: 338px;
    margin: 0;
    text-align: center;
    font-size: 19px;
    font-style: italic;
    color: var(--card-light);
    letter-spacing: 11px;
    white-space: nowrap;
  }
</style>
</head>
<body>
  <section class="card card-front">
    <h1 class="company-name">Fen Athletics</h1>

    <svg class="web-band" width="720" height="412" viewBox="0 0 720 412" aria-hidden="true">
      <path d="M394 223 H720 V269 H366 Q380 224 394 223 Z" fill="var(--accent-red)"/>
      <line x1="46" y1="269.5" x2="720" y2="269.5" stroke="var(--accent-red)" stroke-width="1.5"/>
    </svg>

    <p class="person-name">LEO PEMBERTON-HALE</p>
    <p class="person-role">Operations Manager</p>
    <span class="band-url">www.fenathletics.co.uk</span>

    <ul class="contact-list">
      <li class="contact-item">
        <svg viewBox="0 0 24 24" aria-hidden="true"><path fill="var(--accent-red)" d="M6.6 10.8a15.1 15.1 0 0 0 6.6 6.6l2.2-2.2c.3-.3.7-.4 1-.2 1.1.4 2.3.6 3.6.6.6 0 1 .4 1 1V20c0 .6-.4 1-1 1C10.6 21 3 13.4 3 4c0-.6.4-1 1-1h3.5c.6 0 1 .4 1 1 0 1.3.2 2.5.6 3.6.1.3 0 .7-.2 1z"/></svg>
        (+44) 1632 960 418
      </li>
      <li class="contact-item">
        <svg viewBox="0 0 24 24" aria-hidden="true"><rect x="3" y="6" width="18" height="12" fill="var(--accent-red)"/><path d="M3 6l9 7 9-7" fill="none" stroke="#fff" stroke-width="1.5"/></svg>
        Leo@fenathletics.co.uk
      </li>
      <li class="contact-item">
        <svg viewBox="0 0 24 24" aria-hidden="true"><path fill="var(--accent-red)" d="M12 2a7 7 0 0 0-7 7c0 5.2 7 13 7 13s7-7.8 7-13a7 7 0 0 0-7-7zm0 9.5A2.5 2.5 0 1 1 12 6.5a2.5 2.5 0 0 1 0 5z"/></svg>
        Low Mill, Ashby Fen, Ely, CB7 4QT
      </li>
    </ul>
  </section>

  <section class="card card-back">
    <div class="brand-row">
      <span class="brand">Fen</span>
      <span class="brand"><span class="brand-mark mark-circle"></span>TavaPuni</span>
      <span class="brand"><span class="brand-mark mark-square-purple"></span>ElmStretch</span>
      <span class="brand"><span class="brand-mark mark-square-red"></span>Grit and Rain</span>
    </div>
    <p class="back-url">www.fenathletics.co.uk</p>
  </section>
</body>
</html>
```